Velmo Swinger site - new website, blogsite and merchandise point, connection to tradeva

We are a well established Swingers Club in the North east of UK and already have an existing site. www.velmo-example.co.uk, BUT we have changed our logo and our information on the site needs to be updated.

We are changing our hosting site to Nimbrashost.example ,also wanting to start a blog which is linked to the club, plus we wish to sell a small exclusive range of Velmo linked merchandise which will also be available on Tradeva.

I have attached a pdf of the majority of the content. additionally we will provide pictures and a videoclip which should be able to be viewed by pc's, lap tops and mobile phones (the whole website must be fully accessible via phone).

The new site must be able to be updated by someone with medium computer knowledge (usually me), by no means expert. Updates will generally be new pictures and written information. The site must be able to be transferred to NimbrasHost.

Velmo is one of the countries leading clubs and emphasises friendliness, fun & safety for its members, we look after you to ensure your experience is the best we can offer. We are very proud of our reputation, built up over more than 10 years.

Target Market(s)

Swingers, dreamers & fantasists, alternative lifestyle people

Coding

Coded - Design and coding required

Number of Pages Required

5+ page

Font styles to use
Sans Serif

Colors
000000
ec1f27
fbfbfb
eeeeee
eaeaea

Requirements
Must have
• website with blog attached, link to tradeva & quidlo, ability to run videoclip and picture album and must be compatable to transfer easily to Nimbrashost and be updated by non-professional (who can learn)
• Straightforward & easy to navigate
• over 18 content page with enter button
Nice to have
• sexy site
• link to chirpster maybe
• black site would be nice with red or white writing
Should not have
• children and animals in anyway shape or form

```html
<!DOCTYPE html>
<html lang="en">
<head>
<meta charset="utf-8">
<title>Velmo – Home</title>
<link rel="stylesheet" href="https://fonts.googleapis.com/css2?family=Roboto:wght@300;400;500&family=Roboto+Slab:wght@300;400&display=swap">
<style>
:root{
  --red:#ec1f27;
  --black:#000000;
  --header-dark:#1f1513;
  --footer-dark:#222222;
  --light:#fbfbfb;
  --grey-band:#f4f5f7;
  --line:#eaeaea;
  --text:#444444;
  --muted:#777777;
  --white:#ffffff;
}
*{margin:0;padding:0;box-sizing:border-box}
html,body{width:1200px;height:2278px;overflow:hidden}
body{font-family:"Roboto",Arial,sans-serif;color:var(--text);background:var(--white);position:relative}
.site-header{height:88px;background:var(--header-dark);position:relative}
.brand{position:absolute;left:87px;top:18px;font-family:"Roboto",sans-serif;font-weight:300;font-size:44px;color:var(--white);letter-spacing:2px;line-height:52px}
.main-nav{height:56px;background:var(--red);display:flex;justify-content:center;align-items:center;gap:56px}
.main-nav a{color:var(--white);text-decoration:none;font-size:13px;font-weight:500;text-transform:uppercase}
.hero{position:relative;height:491px;background:radial-gradient(ellipse at 55% 25%,#a25cc4 0%,#5a2a78 35%,#2a1538 70%,#1a0f22 100%);text-align:center;color:var(--white)}
.hero-title{position:absolute;top:146px;left:0;right:0;font-family:"Roboto",sans-serif;font-weight:300;font-size:62px;letter-spacing:4px}
.hero-text{position:absolute;top:232px;left:0;right:0;font-family:"Roboto Slab",serif;font-weight:300;font-size:16px;line-height:31px;text-transform:uppercase}
.btn{display:inline-block;color:var(--white);text-decoration:none;font-size:14px;font-weight:500;text-transform:uppercase;text-align:center}
.btn-red{background:var(--red)}
.btn-grey{background:#555555}
.hero .btn{position:absolute;left:532px;top:318px;width:136px;height:44px;line-height:44px;font-family:"Roboto Slab",serif;font-weight:400}
.hero-arrow{position:absolute;top:363px;width:52px;height:52px}
.hero-arrow.prev{left:24px}.hero-arrow.next{right:24px}
.welcome{height:317px;text-align:center;position:relative}
.section-title{font-size:21px;font-weight:400;color:#333;text-transform:uppercase}
.welcome .section-title{position:absolute;top:44px;left:0;right:0}
.welcome .lead{position:absolute;top:88px;left:0;right:0;color:var(--red);font-size:14px;font-weight:300;text-transform:uppercase}
.welcome .intro{position:absolute;top:128px;left:197px;width:806px;font-size:12px;line-height:25.5px;color:#333}
.welcome .actions{position:absolute;top:234px;left:0;right:0;display:flex;justify-content:center;gap:11px}
.welcome .btn{height:44px;line-height:44px}
.merch{height:476px;background:var(--grey-band);position:relative;text-align:center}
.merch .section-title,.blog .section-title{position:absolute;top:36px;left:0;right:0}
.section-sub{position:absolute;top:77px;left:0;right:0;font-size:12px;color:var(--muted)}
.product-grid{position:absolute;top:125px;left:85px;display:flex;gap:14px}
.product-card{width:247px;height:301px;background:var(--white);border:1px solid var(--line);position:relative}
.shop-label{position:absolute;left:11px;top:18px;font-size:18px;font-weight:500;color:#111}
.product-img{position:absolute;left:30px;top:46px;width:185px;height:168px;border-radius:4px}
.product-card h3{position:absolute;top:229px;left:0;right:0;font-size:15px;font-weight:400;color:#333}
.product-card p{position:absolute;top:253px;left:0;right:0;font-size:12px;color:#444}
.blog{height:504px;position:relative;text-align:center}
.post-grid{position:absolute;top:117px;left:85px;display:flex;gap:21px;text-align:left}
.post{width:330px}
.post-img{height:196px}
.post h3{margin-top:26px;font-size:15px;font-weight:500;color:#333;text-transform:uppercase}
.post p{margin-top:14px;font-size:12px;line-height:23px;color:#444;width:260px}
.post-meta{margin-top:8px;font-family:"Roboto Slab",serif;font-style:normal;font-size:12px;color:var(--red);display:flex;gap:10px;align-items:center}
.post-meta svg{vertical-align:-2px;margin-right:5px}
.partners{height:117px;background:var(--red);display:flex;align-items:center;justify-content:center;gap:34px}
.partner{width:143px;height:74px;border:1px solid rgba(255,255,255,.6);display:flex;align-items:center;justify-content:center;color:var(--white);font-size:20px;font-weight:500}
.site-footer{height:229px;background:var(--footer-dark);position:relative;text-align:center}
.social{position:absolute;top:32px;left:0;right:0;display:flex;justify-content:center;gap:12px}
.social a{width:60px;height:60px;border:1px solid #888;border-radius:50%;display:flex;align-items:center;justify-content:center;color:var(--white);text-decoration:none;font-size:9px}
.footer-rule{position:absolute;top:106px;left:85px;right:85px;border-top:1px solid #3a3a3a}
.footer-nav{position:absolute;top:132px;left:0;right:0;display:flex;justify-content:center;font-family:"Roboto Slab",serif;font-size:12px}
.footer-nav a{color:#ddd;text-decoration:none;text-transform:uppercase;padding:0 21px;border-left:1px solid #aaa;line-height:12px}
.footer-nav a:first-child{border-left:none}
.copyright{position:absolute;top:174px;left:0;right:0;font-family:"Roboto Slab",serif;font-size:12px;color:#ccc}
</style>
</head>
<body>
<header class="site-header">
  <div class="brand">VELMO</div>
</header>
<nav class="main-nav">
  <a href="#">Home</a><a href="#">Diary</a><a href="#">Theme Parties</a><a href="#">TV/TG &amp; Admirers</a><a href="#">Membership</a><a href="#">FAQs</a><a href="#">Rooms</a><a href="#">Contact Us</a>
</nav>
<section class="hero" role="img" aria-label="Crowded nightclub dance floor under purple stage lights">
  <h1 class="hero-title">VELMO</h1>
  <p class="hero-text">Velmo is one of the countries leading clubs and&amp; emphasises<br>friendliness, fun &amp; safety for its members.</p>
  <a class="btn btn-red" href="#">Join to Club</a>
  <svg class="hero-arrow prev" viewBox="0 0 52 52"><circle cx="26" cy="26" r="25" fill="none" stroke="#fff" stroke-width="2"/><path d="M29 18l-8 8 8 8" fill="none" stroke="#fff" stroke-width="3"/></svg>
  <svg class="hero-arrow next" viewBox="0 0 52 52"><circle cx="26" cy="26" r="25" fill="none" stroke="#fff" stroke-width="2"/><path d="M23 18l8 8-8 8" fill="none" stroke="#fff" stroke-width="3"/></svg>
</section>
<section class="welcome">
  <h2 class="section-title">Welcome to Velmo</h2>
  <p class="lead">Velmo is one of the countries leading clubs and emphasises friendliness, fun &amp; safety for its members.</p>
  <p class="intro">New members (Couples and Single guys) - (annual) £30, this now includes the next 2 visits half price. (Single Girls membership si £10; this membership uis discounted to encourage single ladies to join as there are not as many as couples &amp; guys). Renewals remain at £20 New members who are introdu ced, vouched for &amp; come and join with esisting members - members will receive half price entry on that night.</p>
  <div class="actions">
    <a class="btn btn-red" href="#" style="width:135px">Read More</a>
    <a class="btn btn-grey" href="#" style="width:136px">Our Featured</a>
  </div>
</section>
<section class="merch">
  <h2 class="section-title">Merchandise Products</h2>
  <p class="section-sub">It is with regret that we have to increase some of our charges, this is due, in the main, to increased running costs</p>
  <div class="product-grid">
    <article class="product-card"><span class="shop-label">tradeva</span><div class="product-img" role="img" aria-label="Navy t-shirt" style="background:radial-gradient(circle,#2d3f63 0%,#2d3f63 45%,#fff 72%)"></div><h3>T-SHIRTS</h3><p>We make changes as we are always</p></article>
    <article class="product-card"><span class="shop-label">tradeva</span><div class="product-img" role="img" aria-label="White mug" style="background:radial-gradient(circle,#e6e6e6 0%,#f2f2f2 45%,#fff 72%)"></div><h3>MUGS</h3><p>We make changes as we are always</p></article>
    <article class="product-card"><span class="shop-label">tradeva</span><div class="product-img" role="img" aria-label="Yellow travel bag" style="background:radial-gradient(circle,#f4c722 0%,#f4c722 40%,#fff 70%)"></div><h3>BAGS</h3><p>We make changes as we are always</p></article>
    <article class="product-card"><span class="shop-label">tradeva</span><div class="product-img" role="img" aria-label="Two drink cans" style="background:radial-gradient(circle,#3aa0a8 0%,#8bbd3a 45%,#fff 72%)"></div><h3>DRINKS</h3><p>We make changes as we are always</p></article>
  </div>
</section>
<section class="blog">
  <h2 class="section-title">Latest Blog</h2>
  <p class="section-sub">It is with regret that we have to increase some of our charges, this is due, in the main, to increased running costs</p>
  <div class="post-grid">
    <article class="post"><div class="post-img" role="img" aria-label="Candlelit lounge with sofas" style="background:linear-gradient(135deg,#c07a2a,#5a2a12 60%,#1e0e08)"></div><h3>Redwing is the North East's biggest</h3><p>The unlicensed bar serves a variety of hot and cold soft drinks at reasonable prices.</p><div class="post-meta"><span><svg width="11" height="11" viewBox="0 0 11 11"><rect x="0.5" y="1.5" width="10" height="9" fill="none" stroke="#ec1f27"/><path d="M0.5 4h10M3 0v3M8 0v3" stroke="#ec1f27"/></svg>1 month ago</span><span><svg width="12" height="11" viewBox="0 0 12 11"><path d="M1 1h10v6H5l-3 3V7H1z" fill="none" stroke="#ec1f27"/></svg>05 Comments</span></div></article>
    <article class="post"><div class="post-img" role="img" aria-label="Red-lit room with large wooden wheel" style="background:linear-gradient(135deg,#8a2a1a,#3e120c 60%,#1a0806)"></div><h3>Comfortable Environment</h3><p>The unlicensed bar serves a variety of hot and cold soft drinks at reasonable prices.</p><div class="post-meta"><span><svg width="11" height="11" viewBox="0 0 11 11"><rect x="0.5" y="1.5" width="10" height="9" fill="none" stroke="#ec1f27"/><path d="M0.5 4h10M3 0v3M8 0v3" stroke="#ec1f27"/></svg>1 month ago</span><span><svg width="12" height="11" viewBox="0 0 12 11"><path d="M1 1h10v6H5l-3 3V7H1z" fill="none" stroke="#ec1f27"/></svg>05 Comments</span></div></article>
    <article class="post"><div class="post-img" role="img" aria-label="Red and black themed club room" style="background:linear-gradient(135deg,#7a1a14,#2a0c0a 55%,#b08070)"></div><h3>Premises in County Durham</h3><p>The unlicensed bar serves a variety of hot and cold soft drinks at reasonable prices.</p><div class="post-meta"><span><svg width="11" height="11" viewBox="0 0 11 11"><rect x="0.5" y="1.5" width="10" height="9" fill="none" stroke="#ec1f27"/><path d="M0.5 4h10M3 0v3M8 0v3" stroke="#ec1f27"/></svg>1 month ago</span><span><svg width="12" height="11" viewBox="0 0 12 11"><path d="M1 1h10v6H5l-3 3V7H1z" fill="none" stroke="#ec1f27"/></svg>05 Comments</span></div></article>
  </div>
</section>
<section class="partners">
  <div class="partner">Lumora</div><div class="partner">Quenta</div><div class="partner">Tunebay</div><div class="partner">Boxmint</div><div class="partner">Orvane</div><div class="partner">Stockvale</div>
</section>
<footer class="site-footer">
  <div class="social">
    <a href="#">Frendo</a><a href="#">chirpster</a><a href="#">Circlo</a><a href="#">Workly</a><a href="#">Snapo</a>
    <a href="#" aria-label="Email"><svg width="16" height="12" viewBox="0 0 16 12"><rect x="0.75" y="0.75" width="14.5" height="10.5" rx="1" fill="none" stroke="#fff" stroke-width="1.5"/><path d="M1 1.5l7 5 7-5" fill="none" stroke="#fff" stroke-width="1.5"/></svg></a>
  </div>
  <div class="footer-rule"></div>
  <nav class="footer-nav">
    <a href="#">Home</a><a href="#">Diary</a><a href="#">Theme Parties</a><a href="#">TV/TG and Admirers</a><a href="#">Membership</a><a href="#">FAQs</a><a href="#">Rooms</a><a href="#">Contact Us</a>
  </nav>
  <p class="copyright">© Copyrights 2017 Velmo.All Rights Reserved.</p>
</footer>
</body>
</html>
```